Business Card Design

We are a commercial real estate brokerage in San Francisco, leasing office buildings downtown.
I would like a clean, elegant look. Simple but powerful .

Industry/Entity Type

Business

Contact Information for Business Card

Derek Holloway
lic# 07258143
415.555.0172
derek@velt-commercial.example
velt-commercial.example

```html
<!DOCTYPE html>
<html lang="en">
<head>
<meta charset="utf-8">
<title>Velt Commercial — Business Card</title>
<link rel="stylesheet" href="https://fonts.googleapis.com/css2?family=Jost:wght@500;600&family=Roboto+Condensed:wght@400&display=swap">
<style>
  :root {
    --backdrop: #d9c59d;
    --paper: #ffffff;
    --slate: #7889a8;
    --ink: #262626;
    --on-dark: #ffffff;
  }
  * { margin: 0; padding: 0; box-sizing: border-box; }
  html, body {
    width: 1200px;
    height: 1019px;
    overflow: hidden;
    background: var(--backdrop);
  }
  .card {
    position: absolute;
    top: 300px;
    width: 245px;
    height: 418px;
    background: var(--paper);
    box-shadow: 6px 8px 14px rgba(0, 0, 0, 0.18);
    overflow: hidden;
  }
  .card--front { left: 321px; }
  .card--back { left: 634px; }
  .card__shapes {
    position: absolute;
    inset: 0;
    width: 245px;
    height: 418px;
  }
  .wordmark {
    position: absolute;
    top: 156px;
    left: 0;
    width: 245px;
    display: flex;
    justify-content: center;
    align-items: center;
    gap: 8px;
  }
  .wordmark__square {
    width: 12px;
    height: 12px;
    background: var(--slate);
  }
  .wordmark__name {
    font-family: "Jost", sans-serif;
    font-weight: 500;
    font-size: 19px;
    letter-spacing: 0.5px;
    color: var(--slate);
  }
  .holder-name {
    position: absolute;
    top: 144px;
    left: 0;
    width: 245px;
    text-align: center;
    font-family: "Jost", sans-serif;
    font-weight: 600;
    font-size: 15px;
    letter-spacing: 0.4px;
    color: var(--slate);
  }
  .contact-list {
    position: absolute;
    top: 234px;
    left: 0;
    width: 245px;
    list-style: none;
  }
  .contact-row {
    position: relative;
    height: 46px;
    display: flex;
    align-items: center;
    font-family: "Roboto Condensed", sans-serif;
    font-size: 10.5px;
    color: var(--on-dark);
  }
  .contact-row--dark { background: var(--ink); }
  .contact-row--slate { background: var(--slate); }
  .contact-row__icon {
    position: absolute;
    left: 41px;
    width: 14px;
    height: 14px;
  }
  .contact-row__text {
    position: absolute;
    left: 75px;
  }
  .contact-row__pointer {
    position: absolute;
    left: 220px;
    width: 5px;
    height: 7px;
  }
</style>
</head>
<body>

<section class="card card--front" aria-label="Card front">
  <svg class="card__shapes" viewBox="0 0 245 418" aria-hidden="true">
    <polygon points="0,0 245,0 245,50" fill="var(--slate)"/>
    <polygon points="0,0 58,13 0,32" fill="var(--ink)"/>
    <polygon points="0,288 245,238 245,418 0,418" fill="var(--slate)"/>
    <polygon points="0,257 57,276 0,288" fill="var(--ink)"/>
  </svg>
  <div class="wordmark">
    <span class="wordmark__square"></span>
    <span class="wordmark__name">VELT COMMERCIAL</span>
  </div>
</section>

<section class="card card--back" aria-label="Card back">
  <svg class="card__shapes" viewBox="0 0 245 418" aria-hidden="true">
    <polygon points="0,0 245,0 245,50" fill="var(--slate)"/>
    <polygon points="0,0 58,13 0,32" fill="var(--ink)"/>
    <polygon points="0,234 0,222 245,183 245,234" fill="var(--slate)"/>
    <polygon points="0,203 57,221 0,232" fill="var(--ink)"/>
  </svg>

  <h1 class="holder-name">DEREK HOLLOWAY</h1>

  <ul class="contact-list">
    <li class="contact-row contact-row--dark">
      <span class="contact-row__text">lic# 07258143</span>
      <svg class="contact-row__pointer" viewBox="0 0 5 7"><polygon points="5,0 0,3.5 5,7" fill="var(--on-dark)"/></svg>
    </li>
    <li class="contact-row contact-row--slate">
      <svg class="contact-row__icon" viewBox="0 0 14 14" aria-hidden="true">
        <rect x="4" y="1" width="6" height="12" rx="1" fill="none" stroke="var(--ink)" stroke-width="1"/>
        <line x1="6" y1="11" x2="8" y2="11" stroke="var(--ink)" stroke-width="0.8"/>
      </svg>
      <span class="contact-row__text">415.555.0172</span>
      <svg class="contact-row__pointer" viewBox="0 0 5 7"><polygon points="5,0 0,3.5 5,7" fill="var(--on-dark)"/></svg>
    </li>
    <li class="contact-row contact-row--dark">
      <svg class="contact-row__icon" viewBox="0 0 14 14" aria-hidden="true">
        <rect x="1.5" y="3.5" width="11" height="7" fill="none" stroke="var(--slate)" stroke-width="0.9"/>
        <polyline points="1.5,3.5 7,8 12.5,3.5" fill="none" stroke="var(--slate)" stroke-width="0.9"/>
      </svg>
      <span class="contact-row__text">derek@velt-commercial.example</span>
      <svg class="contact-row__pointer" viewBox="0 0 5 7"><polygon points="5,0 0,3.5 5,7" fill="var(--on-dark)"/></svg>
    </li>
    <li class="contact-row contact-row--slate">
      <svg class="contact-row__icon" viewBox="0 0 14 14" aria-hidden="true">
        <circle cx="7" cy="7" r="5.5" fill="none" stroke="var(--ink)" stroke-width="1"/>
        <ellipse cx="7" cy="7" rx="2.3" ry="5.5" fill="none" stroke="var(--ink)" stroke-width="0.8"/>
        <line x1="1.5" y1="7" x2="12.5" y2="7" stroke="var(--ink)" stroke-width="0.8"/>
      </svg>
      <span class="contact-row__text">velt-commercial.example</span>
      <svg class="contact-row__pointer" viewBox="0 0 5 7"><polygon points="5,0 0,3.5 5,7" fill="var(--on-dark)"/></svg>
    </li>
  </ul>
</section>

</body>
</html>
```